Personal Motivational Quote Poster Design

I would like to create a poster with some of my favorite quotes to hang in my office. I did similar projects in 2012 and 2014. I've uploaded the winning designs so you can get a better idea of what I'm looking for. I will provide feedback on your design within 24 hours of receiving it.

The poster must contain the following quotes:

“What the pupil must learn, if he learns anything at all, is that the world will do most of the work for you, provided you cooperate with it by identifying how it really works and aligning with those realities. If we do not let the world teach us, it teaches us a lesson.” - Harold Quenby

“I tackle every big new problem by asking two questions: Who has dealt with this problem well? And what can we learn from them?” - Walt Prisco

“If we can really understand the problem, the answer will come out of it, because the answer is not separate from the problem.” - Ravindra Selvapathi

“Success is nothing more than a few simple disciplines, practiced every day; while failure is simply a few errors in judgment, repeated every day. It is the accumulative weight of our disciplines and our judgments that leads us to either fortune or failure.” - Ned Falco

“Inaction breeds doubt and fear. Action breeds confidence and courage.” - Rufus Pembrook

“What’s the one thing you can do, such that by doing it, everything else will be easier or unnecessary?” - Lyle Dorsey

Requirements
Must have
• The poster will be 24" high x 36" long and printed on canvas, so the image you create needs to have a resolution of at least 2700 x 3900.
Nice to have
• I don't have an exact vision for how the poster should look, so I am totally open to you using your creativity to develop, arrange and present the content as you'd like.

That said, I would like an image (photo or posterized image) of the person being quoted along with each quote. I do not have specific images that I would like you to use, so you will need to find the images on your own.

The images don't need to be perfect... I am more interested in the poster relating the essence of the quotes and the people being quoted than I am in perfect photographic images of the people being quoted.

```html
<!DOCTYPE html>
<html lang="en">
<head>
<meta charset="utf-8">
<title>Motivational Quote Poster</title>
<link rel="stylesheet" href="https://fonts.googleapis.com/css2?family=Raleway:ital,wght@0,900;1,400;1,600;1,700&display=swap">
<style>
  :root {
    --backdrop: #dcdcdc;
    --wall: #f5f5f4;
    --ink: #1b1b1b;
    --green: #1ea57b;
    --green-deep: #0f6b4f;
    --red: #e8383d;
    --red-deep: #9e1f24;
    --pink: #e052a3;
    --pink-deep: #8e2f66;
    --orange: #f3a61d;
    --orange-deep: #a9661a;
  }
  html, body { margin: 0; padding: 0; }
  body {
    width: 975px; height: 1200px; overflow: hidden;
    background: var(--backdrop);
    font-family: "Raleway", sans-serif;
    color: var(--ink);
  }
  .poster {
    position: absolute; left: 87px; top: 0;
    width: 800px; height: 1200px;
    background: var(--wall);
    overflow: hidden;
  }
  .shapes { position: absolute; inset: 0; }
  .quote {
    position: absolute; margin: 0;
    font-style: italic; font-weight: 400;
    font-size: 11.5px; line-height: 1.6;
  }
  .quote--light { color: #fff; }
  .author {
    position: absolute; margin: 0;
    font-style: italic; font-weight: 700; font-size: 12.5px;
    white-space: nowrap;
  }
  .author--red { color: var(--red); }
  .author--green { color: var(--green); }
  .mark {
    position: absolute; margin: 0;
    font-family: "Raleway", sans-serif; font-weight: 900;
    font-size: 78px; line-height: 1; letter-spacing: -4px;
  }
</style>
</head>
<body>
<main class="poster">
  <svg class="shapes" width="800" height="1200" viewBox="0 0 800 1200">
    <defs>
      <radialGradient id="toneGreen" cx="50%" cy="45%" r="60%"><stop offset="0" stop-color="#cfcfcf"/><stop offset="1" stop-color="#0f6b4f"/></radialGradient>
      <radialGradient id="toneGrey" cx="45%" cy="45%" r="60%"><stop offset="0" stop-color="#d9d9d9"/><stop offset="1" stop-color="#5e5e5e"/></radialGradient>
      <radialGradient id="toneRed" cx="50%" cy="40%" r="60%"><stop offset="0" stop-color="#e9b89d"/><stop offset="1" stop-color="#9e1f24"/></radialGradient>
      <radialGradient id="tonePink" cx="50%" cy="40%" r="60%"><stop offset="0" stop-color="#b98aa8"/><stop offset="1" stop-color="#8e2f66"/></radialGradient>
      <radialGradient id="toneOrange" cx="50%" cy="40%" r="60%"><stop offset="0" stop-color="#e7a37a"/><stop offset="1" stop-color="#a9661a"/></radialGradient>
    </defs>

    <!-- green block -->
    <path class="blob blob--green" fill="var(--green)" d="M70,150 C100,90 250,100 330,100 C420,100 470,130 460,230 C455,300 420,335 330,330 C230,325 120,340 70,300 C30,265 40,200 70,150Z"/>
    <path class="blob-line" fill="none" stroke="var(--ink)" stroke-width="2.5" d="M60,120 C140,60 380,70 450,120 C490,150 470,240 450,300 C430,345 300,340 200,335 C100,330 40,300 45,230 C48,180 40,140 60,120Z"/>
    <ellipse role="img" aria-label="Portrait of Harold Quenby" cx="145" cy="215" rx="72" ry="88" fill="url(#toneGreen)"/>

    <!-- red frame -->
    <rect class="frame" x="488" y="90" width="244" height="230" rx="60" fill="none" stroke="var(--red)" stroke-width="2"/>
    <rect class="frame" x="492" y="86" width="240" height="234" rx="64" fill="none" stroke="var(--red)" stroke-width="1.5" transform="rotate(-1.5 612 203)"/>
    <rect role="img" aria-label="Portrait of Rufus Pembrook" x="628" y="124" width="96" height="160" rx="44" fill="url(#toneGrey)"/>

    <!-- red block -->
    <path class="blob blob--red" fill="var(--red)" d="M190,420 C250,360 430,370 520,390 C600,405 600,470 590,530 C580,610 520,640 420,630 C320,620 220,640 180,580 C150,530 150,460 190,420Z"/>
    <path class="blob-line" fill="none" stroke="var(--ink)" stroke-width="2.5" d="M145,430 C170,360 340,370 430,360 C540,350 620,370 620,450 C620,530 560,590 460,590 C360,590 240,620 180,580 C140,550 130,490 145,430Z"/>
    <ellipse role="img" aria-label="Portrait of Walt Prisco" cx="256" cy="492" rx="70" ry="95" fill="url(#toneRed)"/>

    <!-- green frame -->
    <rect class="frame" x="488" y="628" width="244" height="198" rx="8" fill="none" stroke="var(--green)" stroke-width="2"/>
    <rect class="frame" x="492" y="624" width="240" height="204" rx="10" fill="none" stroke="var(--green)" stroke-width="1.5" transform="rotate(1.2 612 726)"/>
    <rect role="img" aria-label="Portrait of Lyle Dorsey" x="642" y="653" width="84" height="140" rx="36" fill="url(#toneGrey)"/>

    <!-- pink block -->
    <path class="blob blob--pink" fill="var(--pink)" d="M40,800 C50,730 150,700 260,705 C370,710 440,740 440,820 C440,900 380,940 260,935 C150,930 40,900 40,800Z"/>
    <path class="blob-line" fill="none" stroke="var(--ink)" stroke-width="2.5" d="M50,740 C100,670 330,660 420,690 C470,710 475,800 450,860 C420,915 300,925 200,922 C100,920 45,870 48,810 C50,780 45,755 50,740Z"/>
    <ellipse role="img" aria-label="Portrait of Ravindra Selvapathi" cx="118" cy="823" rx="66" ry="95" fill="url(#tonePink)"/>

    <!-- orange block -->
    <path class="blob blob--orange" fill="var(--orange)" d="M360,960 C380,900 500,895 600,905 C700,915 720,960 715,1060 C710,1150 650,1185 530,1185 C420,1185 350,1160 345,1080 C342,1030 345,990 360,960Z"/>
    <path class="blob-line" fill="none" stroke="var(--ink)" stroke-width="2.5" d="M330,950 C410,870 630,870 695,930 C730,965 735,1060 705,1125 C675,1180 560,1185 470,1180 C370,1175 322,1130 326,1060 C327,1010 324,970 330,950Z"/>
    <ellipse role="img" aria-label="Portrait of Ned Falco" cx="622" cy="1001" rx="55" ry="74" fill="url(#toneOrange)"/>
  </svg>

  <!-- Harold Quenby -->
  <p class="quote quote--light" style="left:228px;top:120px;width:220px;text-align:center;">“What the pupil must learn, if he learns anything at all, is that the world will do most of the work for you, provided you cooperate with it by identifying how it really works and aligning with those realities. If we do not let the world teach us, it teaches us a lesson.”</p>
  <p class="author" style="left:256px;top:275px;">Harold Quenby</p>
  <p class="mark" style="left:382px;top:258px;">”</p>

  <!-- Rufus Pembrook -->
  <p class="mark" style="left:518px;top:84px;color:var(--red);">“</p>
  <p class="quote" style="left:518px;top:150px;width:100px;">“Inaction breeds doubt and fear. Action breeds confidence and courage.”</p>
  <p class="author author--red" style="left:518px;top:245px;">Rufus Pembrook</p>
  <p class="mark" style="left:668px;top:282px;color:var(--red);">”</p>

  <!-- Walt Prisco -->
  <p class="quote quote--light" style="left:350px;top:425px;width:230px;text-align:center;">“I tackle every big new problem by asking two questions: Who has dealt with this problem well? And what can we learn from them?”</p>
  <p class="author" style="left:418px;top:527px;">Walt Prisco</p>
  <p class="mark" style="left:512px;top:514px;">”</p>

  <!-- Lyle Dorsey -->
  <p class="mark" style="left:515px;top:622px;color:var(--green);">“</p>
  <p class="quote" style="left:518px;top:688px;width:118px;">“What’s the one thing you can do, such that by doing it, everything else will be easier or unnecessary?”</p>
  <p class="author author--green" style="left:518px;top:792px;">Lyle Dorsey</p>
  <p class="mark" style="left:668px;top:796px;color:var(--green);">”</p>

  <!-- Ravindra Selvapathi -->
  <p class="quote quote--light" style="left:196px;top:732px;width:200px;text-align:center;">“If we can really understand the problem, the answer will come out of it, because the answer is not separate from the problem.”</p>
  <p class="author" style="left:232px;top:818px;">Ravindra Selvapathi</p>
  <p class="mark" style="left:322px;top:842px;">”</p>

  <!-- Ned Falco -->
  <p class="quote quote--light" style="left:372px;top:935px;width:180px;">“Success is nothing more than a few simple disciplines, practiced every day; while failure is simply a few errors in judgment, repeated every day. It is the accumulative weight of our disciplines and our judgments that leads us to either fortune or failure.”</p>
  <p class="author" style="left:380px;top:1112px;">Ned Falco</p>
  <p class="mark" style="left:640px;top:1062px;">”</p>
</main>
</body>
</html>
```